Unique Business Card Design

Unique Business Card design for our orthotic and prosthetic company. Our logo is on our website, color is light blue. Unique shape (artificial leg shaped, vertical, etc..) preferred. Logo, business name, individual name and basic demographics needed.

Industry/Entity Type

Business

Contact Information for Business Card

Logo, Industry, Phone # Logo, "Prosthetic & Orthotic Services" Place to add individual name and contact info

Colors
cee9f5

Requirements
Must have
• The icon must be there, placement of "Prosthetic & Orthotic Services" can be moved
Nice to have
• Like the mix of light blue, and a little darker blue. One design included the icons from my website which was a nice touch

```html
<!DOCTYPE html>
<html lang="en">
<head>
<meta charset="utf-8">
<title>Limbwell Inc. Business Card</title>
<link href="https://fonts.googleapis.com/css2?family=Arimo:wght@400;700&display=swap" rel="stylesheet">
<style>
  :root {
    --backdrop: #3b3531;
    --card: #161718;
    --card-edge: #222426;
    --blue: #2f6db2;
    --blue-light: #4a8ad0;
    --text: #dfe2e5;
    --rule: #7d8186;
  }
  * { box-sizing: border-box; margin: 0; padding: 0; }
  html, body {
    width: 1200px; height: 864px; overflow: hidden;
    background: var(--backdrop);
    font-family: "Arimo", Arial, sans-serif;
  }
  .stage { position: relative; width: 1200px; height: 864px; }
  .card {
    position: absolute; top: 280px;
    width: 530px; height: 303px;
    background: var(--card);
    border: 1px solid var(--card-edge);
    box-shadow: 0 10px 30px rgba(0,0,0,.45);
    color: var(--text);
  }
  .card-back { left: 50px; }
  .card-front { left: 620px; }

  /* back */
  .back-mark {
    position: absolute; left: 50%; top: 58px;
    width: 138px; height: 138px; margin-left: -69px;
    border-radius: 50%; background: var(--blue);
  }
  .back-web {
    position: absolute; left: 0; right: 0; top: 232px;
    display: flex; align-items: center; justify-content: center; gap: 14px;
    font-size: 13px; color: #b9bdc2;
  }
  .back-web .rule { width: 130px; height: 1px; background: var(--rule); }

  /* front */
  .holder {
    position: absolute; left: 40px; top: 42px;
    color: var(--blue-light); font-size: 20px;
  }
  .holder .credential { font-size: 13px; margin-left: 4px; }
  .rule-name {
    position: absolute; left: 40px; top: 78px; width: 230px;
    height: 1px; background: var(--rule);
  }
  .contacts { position: absolute; left: 40px; top: 92px; list-style: none; font-size: 14px; }
  .contacts li { display: flex; align-items: center; gap: 8px; height: 21px; }
  .contacts svg { width: 13px; height: 13px; fill: var(--blue-light); }
  .email { position: absolute; left: 40px; top: 182px; font-size: 14px; }

  .brand {
    position: absolute; right: 30px; top: 36px;
    display: flex; align-items: center; gap: 12px;
  }
  .brand-dot { width: 66px; height: 66px; border-radius: 50%; background: var(--blue); }
  .brand-text { display: flex; flex-direction: column; }
  .brand-name {
    font-weight: 700; font-size: 22px; color: var(--blue-light);
    letter-spacing: .5px;
    border-bottom: 2px solid var(--blue-light); padding-bottom: 2px;
  }
  .brand-tagline { font-size: 11px; color: var(--blue-light); margin-top: 4px; }

  .rule-address {
    position: absolute; left: 190px; right: 30px; top: 210px;
    height: 1px; background: var(--rule);
  }
  .address {
    position: absolute; right: 30px; top: 224px;
    text-align: right; font-size: 14px; line-height: 20px; font-style: normal;
  }
</style>
</head>
<body>
<main class="stage">
  <section class="card card-back" aria-label="Card back">
    <div class="back-mark"></div>
    <p class="back-web"><span class="rule"></span>www.limbwellinc.com<span class="rule"></span></p>
  </section>

  <section class="card card-front" aria-label="Card front">
    <h1 class="holder">Mara Lindqvist,<span class="credential">CO LPO</span></h1>
    <div class="rule-name"></div>
    <ul class="contacts">
      <li><svg viewBox="0 0 24 24"><path d="M6.6 10.8a15.1 15.1 0 006.6 6.6l2.2-2.2a1 1 0 011-.25 11.4 11.4 0 003.6.57 1 1 0 011 1V20a1 1 0 01-1 1A17 17 0 013 4a1 1 0 011-1h3.5a1 1 0 011 1c0 1.25.2 2.45.57 3.57a1 1 0 01-.25 1z"/></svg>555.014.2700</li>
      <li><svg viewBox="0 0 24 24"><path d="M7 1h10a2 2 0 012 2v18a2 2 0 01-2 2H7a2 2 0 01-2-2V3a2 2 0 012-2zm0 3v14h10V4z"/></svg>555.014.3919</li>
      <li><svg viewBox="0 0 24 24"><path d="M6 2h10v5H6zM3 8h18a1 1 0 011 1v9a1 1 0 01-1 1h-3v3H6v-3H3a1 1 0 01-1-1V9a1 1 0 011-1zm5 8v4h8v-4z"/></svg>555-0187415</li>
    </ul>
    <p class="email"><svg viewBox="0 0 24 24" width="13" height="13" style="fill:var(--blue-light);vertical-align:-1px;margin-right:8px"><path d="M2 5h20v14H2zm2 2v.5l8 5 8-5V7z"/></svg>mlindqvist@limbwellinc.com</p>

    <div class="brand">
      <div class="brand-dot"></div>
      <div class="brand-text">
        <span class="brand-name">LIMBWELL INC.</span>
        <span class="brand-tagline">Prosthetic &amp; Orthotic Services</span>
      </div>
    </div>

    <div class="rule-address"></div>
    <address class="address">820 Harbor Ave.<br>Eastmoor, NY 10099<br>www.limbwellinc.com</address>
  </section>
</main>
</body>
</html>
```